Local Roofing/Construction company business needs new biz card design

We need a new business card design, current cards are from the start of this operation and generic at best. We are a local Construction Company (General Contractor) with a majority of our work originating from insurance claims-exterior finish work is the main focus (Roofs-Siding-Gutters etc). Heavily involved with homeowners and the low ball offers they receive from insurance company's after a insurable event takes place. I have attached some of our original logo file(s) below.

```html
<!DOCTYPE html>
<html lang="en">
<head>
<meta charset="utf-8">
<title>Stonefield Construction – Business Card</title>
<link href="https://fonts.googleapis.com/css2?family=Montserrat:wght@400;500;600;800&display=swap" rel="stylesheet">
<style>
  :root {
    --canvas: #2b2d2e;
    --card: #03181d;
    --card-deep: #011015;
    --green: #00dc7d;
    --white: #f4f6f5;
    --muted: #6f7a7c;
  }
  * { box-sizing: border-box; margin: 0; padding: 0; }
  html, body { width: 1200px; height: 1200px; overflow: hidden; }
  body {
    background: var(--canvas);
    font-family: "Montserrat", sans-serif;
    display: flex;
    flex-direction: column;
    align-items: center;
    justify-content: center;
    gap: 40px;
  }
  .card {
    position: relative;
    width: 900px;
    height: 514px;
    border-radius: 44px;
    background: radial-gradient(ellipse at 40% 30%, var(--card) 0%, var(--card-deep) 100%);
    border: 2px solid var(--green);
    overflow: hidden;
  }
  /* Front */
  .brand {
    position: absolute;
    top: 110px;
    left: 190px;
    display: flex;
    align-items: center;
    gap: 24px;
  }
  .brand-square {
    width: 78px;
    height: 78px;
    background: var(--green);
  }
  .brand-name {
    color: var(--white);
    font-weight: 800;
    font-size: 44px;
    line-height: 1.02;
    letter-spacing: 2px;
    text-transform: uppercase;
  }
  .divider {
    position: absolute;
    left: 450px;
    top: 290px;
    width: 1px;
    height: 150px;
    background: var(--muted);
  }
  .person {
    position: absolute;
    left: 90px;
    bottom: 70px;
  }
  .person-name {
    color: var(--green);
    font-weight: 600;
    font-size: 44px;
    letter-spacing: 0.5px;
    line-height: 1;
  }
  .person-role {
    color: var(--white);
    font-weight: 400;
    font-size: 22px;
    margin-top: 6px;
    margin-left: 20px;
    letter-spacing: 0.5px;
  }
  .contacts {
    position: absolute;
    left: 500px;
    top: 285px;
    list-style: none;
    display: flex;
    flex-direction: column;
    gap: 12px;
  }
  .contacts li {
    display: flex;
    align-items: flex-start;
    gap: 12px;
    color: var(--white);
    font-size: 19px;
    line-height: 1.2;
  }
  .contacts svg { width: 20px; height: 20px; flex: none; margin-top: 1px; fill: var(--green); }
  /* Back */
  .back-brand {
    position: absolute;
    inset: 0;
    display: flex;
    align-items: center;
    justify-content: center;
    gap: 28px;
  }
  .back-brand .brand-square { width: 110px; height: 110px; }
  .back-brand .brand-name { color: var(--green); font-size: 52px; }
</style>
</head>
<body>
  <section class="card card-front">
    <div class="brand">
      <div class="brand-square"></div>
      <div class="brand-name">Stonefield<br>Construction</div>
    </div>
    <div class="divider"></div>
    <div class="person">
      <div class="person-name">FULL NAME</div>
      <div class="person-role">POSITION</div>
    </div>
    <ul class="contacts">
      <li>
        <svg viewBox="0 0 24 24"><path d="M6.6 10.8a15.1 15.1 0 0 0 6.6 6.6l2.2-2.2c.3-.3.7-.4 1-.2 1.1.4 2.3.6 3.6.6.6 0 1 .4 1 1V20c0 .6-.4 1-1 1A17 17 0 0 1 3 4c0-.6.4-1 1-1h3.5c.6 0 1 .4 1 1 0 1.3.2 2.5.6 3.6.1.3 0 .7-.2 1z"/></svg>
        <span>555-014-2087</span>
      </li>
      <li>
        <svg viewBox="0 0 24 24"><path d="M12 2a10 10 0 1 0 0 20 10 10 0 0 0 0-20zm6.9 6h-2.9a15.6 15.6 0 0 0-1.4-3.6A8 8 0 0 1 18.9 8zM12 4c.8 1.2 1.5 2.5 1.9 4h-3.8c.4-1.5 1.1-2.8 1.9-4zM4.3 14a8.2 8.2 0 0 1 0-4h3.4a16.5 16.5 0 0 0 0 4zm.8 2h2.9c.3 1.3.8 2.5 1.4 3.6A8 8 0 0 1 5.1 16zM8 8H5.1a8 8 0 0 1 4.3-3.6C8.8 5.5 8.3 6.7 8 8zm4 12c-.8-1.2-1.5-2.5-1.9-4h3.8c-.4 1.5-1.1 2.8-1.9 4zm2.3-6H9.7a14.7 14.7 0 0 1 0-4h4.6a14.7 14.7 0 0 1 0 4zm.3 5.6c.6-1.1 1.1-2.3 1.4-3.6h2.9a8 8 0 0 1-4.3 3.6zm1.7-5.6a16.5 16.5 0 0 0 0-4h3.4a8.2 8.2 0 0 1 0 4z"/></svg>
        <span>www.stonefieldbuild.com</span>
      </li>
      <li>
        <svg viewBox="0 0 24 24"><path d="M2 5h20v14H2zm2 2v.5l8 5 8-5V7zm0 2.8V17h16V9.8l-8 5z"/></svg>
        <span>hello@stonefieldbuild.com</span>
      </li>
      <li>
        <svg viewBox="0 0 24 24"><path d="M12 2a7 7 0 0 0-7 7c0 5.2 7 13 7 13s7-7.8 7-13a7 7 0 0 0-7-7zm0 9.5A2.5 2.5 0 1 1 12 6.5a2.5 2.5 0 0 1 0 5z"/></svg>
        <span>42 Birch Hollow Rd<br>Fairview, MO 63000</span>
      </li>
    </ul>
  </section>

  <section class="card card-back">
    <div class="back-brand">
      <div class="brand-square"></div>
      <div class="brand-name">Stonefield<br>Construction</div>
    </div>
  </section>
</body>
</html>
```